Defense contractor needs a roll-up for an exhibition

The booth we have booked has only a size of 3m².
So this will be the centerpiece of the whole booth.
We need a roll-up that attracts visitors and at the same time it should contain already designed graphics. These graphics are giving visitors an overview of our system. So it is necessary to have them exposed in a height that the booth personal can conveniently point with its fingers at them.
For information about our company and product visit:
https://www.brellowtrackline.com/
For designing you should use Adobe Illustrator and the templates provided in the zip file, to guarantee a perfect print.
I have supplied my business card that you can copy the logo. As the company logo will be already at the booth nearby the top of the roll-up, you should not place it there. It can be in the middle or at the bottom.
I have uploaded a picture of the booth. The roll up will be placed at the left of the screen and has a size of 80cm x 200cm

Defense

Defense

Serif

0054AA
0677BA
7BADD7
CADEEF
E8F1F8

• you must use the Adobe Illustrator template to have a good printing result
• company logo on the upper side of the roll-up

```html
<!DOCTYPE html>
<html lang="en">
<head>
<meta charset="utf-8">
<title>Brellow Trackline – VELTRAS Roll-up</title>
<link rel="stylesheet" href="https://fonts.googleapis.com/css2?family=Anton&family=Barlow:wght@500;600;700;800&family=Orbitron:wght@500;600;900&display=swap">
<style>
  :root {
    --stage: #d6d6d8;
    --ink: #141414;
    --ink-soft: #2b2b2b;
    --navy: #1a0d66;
    --purple: #5b0f96;
    --purple-band: #4a1fa0;
    --purple-deep: #2b1a7c;
    --blue: #1f7fcc;
    --blue-light: #8fbde6;
    --white: #ffffff;
  }
  html, body {
    margin: 0;
    width: 676px;
    height: 1200px;
    overflow: hidden;
    background: var(--stage);
  }
  .rollup {
    position: absolute;
    left: 83px;
    top: 0;
    width: 510px;
    height: 1200px;
    display: block;
  }
  .brand-name { font-family: 'Barlow', sans-serif; font-weight: 800; fill: var(--ink); }
  .kicker { font-family: 'Orbitron', sans-serif; font-weight: 500; fill: var(--ink); }
  .headline { font-family: 'Anton', sans-serif; fill: var(--purple); }
  .headline .accent { fill: var(--blue); }
  .product-name { font-family: 'Orbitron', sans-serif; font-weight: 900; fill: var(--navy); }
  .product-full { font-family: 'Barlow', sans-serif; font-weight: 600; fill: var(--ink-soft); }
  .features-title { font-family: 'Orbitron', sans-serif; font-weight: 600; fill: var(--white); }
  .feature-label { font-family: 'Barlow', sans-serif; font-weight: 600; fill: var(--ink-soft); }
  .feature-number { font-family: 'Barlow', sans-serif; font-weight: 800; }
  .note { font-family: 'Barlow', sans-serif; font-weight: 600; fill: var(--ink); }
  .cta { font-family: 'Barlow', sans-serif; font-weight: 700; fill: var(--white); }
  .address { font-family: 'Barlow', sans-serif; font-weight: 700; fill: var(--white); }
  .phone { font-family: 'Barlow', sans-serif; font-weight: 700; fill: var(--white); }
  .web { font-family: 'Barlow', sans-serif; font-weight: 700; fill: var(--white); }
  .feature-frame { fill: var(--white); stroke: var(--blue); stroke-width: 2.5; }
  .feature-cap { fill: var(--blue); }
  .icon { fill: var(--purple-band); }
</style>
</head>
<body>
<svg class="rollup" viewBox="0 0 972 2287" preserveAspectRatio="none" xmlns="http://www.w3.org/2000/svg">
  <defs>
    <linearGradient id="bandGrad" x1="0" x2="1" y1="0" y2="0">
      <stop offset="0" stop-color="#3a1a8c"/>
      <stop offset="0.5" stop-color="#5a22ae"/>
      <stop offset="1" stop-color="#2b1a7c"/>
    </linearGradient>
    <linearGradient id="glowGrad" x1="0" x2="0" y1="0" y2="1">
      <stop offset="0" stop-color="#ffffff"/>
      <stop offset="1" stop-color="#b79ae8"/>
    </linearGradient>
    <linearGradient id="sceneGrad" x1="0" x2="0" y1="0" y2="1">
      <stop offset="0" stop-color="#7fb8de"/>
      <stop offset="0.45" stop-color="#c9c3b0"/>
      <stop offset="0.75" stop-color="#a88a66"/>
      <stop offset="1" stop-color="#6b4c36"/>
    </linearGradient>
    <linearGradient id="numGrad" x1="0" x2="0" y1="0" y2="1">
      <stop offset="0" stop-color="#1f7fcc"/>
      <stop offset="1" stop-color="#4a1fa0"/>
    </linearGradient>
    <linearGradient id="mistGrad" x1="0" x2="0" y1="0" y2="1">
      <stop offset="0" stop-color="#ffffff" stop-opacity="0"/>
      <stop offset="1" stop-color="#c9bde8" stop-opacity="0.55"/>
    </linearGradient>
  </defs>

  <rect width="972" height="2287" fill="#ffffff"/>

  <!-- Header -->
  <text class="brand-name" x="486" y="122" font-size="58" text-anchor="middle" textLength="600" lengthAdjust="spacingAndGlyphs">BRELLOW TRACKLINE</text>
  <text class="kicker" x="486" y="196" font-size="40" text-anchor="middle" textLength="758" lengthAdjust="spacingAndGlyphs">ADVANCED COMBAT TRAINING</text>
  <text class="headline" x="103" y="290" font-size="96" textLength="765" lengthAdjust="spacingAndGlyphs"><tspan class="accent">FOR</tspan> REALISTIC COMBAT</text>
  <text class="headline" x="486" y="390" font-size="96" text-anchor="middle" textLength="400" lengthAdjust="spacingAndGlyphs">SIMULATION</text>

  <!-- Hero band and scene -->
  <polygon points="0,417 482,485 972,403 972,1120 0,1120" fill="url(#bandGrad)"/>
  <polygon points="330,435 482,478 630,435" fill="url(#glowGrad)"/>
  <g role="img" aria-label="Armoured tank firing on a dusty desert road in front of pale buildings">
    <polygon points="0,495 482,523 972,487 972,1060 0,1060" fill="url(#sceneGrad)"/>
  </g>

  <!-- Product section -->
  <polygon points="0,1155 357,1145 0,1185" fill="var(--purple-band)"/>
  <polygon points="620,1145 972,1155 972,1185" fill="var(--purple-band)"/>
  <text class="product-name" x="486" y="1302" font-size="142" text-anchor="middle" textLength="595" lengthAdjust="spacingAndGlyphs">VELTRAS</text>
  <text class="product-full" x="486" y="1340" font-size="30" text-anchor="middle" textLength="730" lengthAdjust="spacingAndGlyphs">(Vehicle Range Tracking &amp; Instrumentation System)</text>

  <polygon points="78,1377 105,1377 78,1455 50,1455" fill="var(--blue-light)"/>
  <polygon points="117,1377 878,1377 853,1455 92,1455" fill="var(--blue)"/>
  <polygon points="893,1377 920,1377 892,1455 865,1455" fill="var(--blue-light)"/>
  <text class="features-title" x="486" y="1436" font-size="52" text-anchor="middle" textLength="672" lengthAdjust="spacingAndGlyphs">FEATURES OF VELTRAS</text>

  <!-- Feature grid: row 1 -->
  <g class="feature" transform="translate(87,1512)">
    <rect class="feature-frame" width="215" height="175"/>
    <polygon class="feature-cap" points="0,0 215,0 215,3 107.5,18 0,3"/>
    <polygon class="feature-cap" points="0,175 215,175 215,172 107.5,157 0,172"/>
    <text class="feature-number" x="107.5" y="88" font-size="76" text-anchor="middle" fill="url(#numGrad)">16</text>
    <text class="feature-label" x="107.5" y="116" font-size="22" text-anchor="middle">16 Camera Systems</text>
    <text class="feature-label" x="107.5" y="143" font-size="22" text-anchor="middle">per vehicle</text>
  </g>
  <g class="feature" transform="translate(380,1512)">
    <rect class="feature-frame" width="215" height="175"/>
    <polygon class="feature-cap" points="0,0 215,0 215,3 107.5,18 0,3"/>
    <polygon class="feature-cap" points="0,175 215,175 215,172 107.5,157 0,172"/>
    <g class="icon" transform="translate(107.5,60)">
      <path d="M-10,-34 a14,14 0 0 1 20,0" fill="none" stroke="var(--purple-band)" stroke-width="3"/>
      <rect x="-17" y="-26" width="34" height="58" rx="8"/>
      <g fill="#ffffff">
        <circle cx="-7" cy="-14" r="2.4"/><circle cx="0" cy="-14" r="2.4"/><circle cx="7" cy="-14" r="2.4"/>
        <circle cx="-7" cy="-6" r="2.4"/><circle cx="0" cy="-6" r="2.4"/><circle cx="7" cy="-6" r="2.4"/>
      </g>
      <circle cx="0" cy="16" r="8" fill="none" stroke="#ffffff" stroke-width="3.5"/>
    </g>
    <text class="feature-label" x="107.5" y="116" font-size="22" text-anchor="middle">Remote-Control</text>
    <text class="feature-label" x="107.5" y="143" font-size="22" text-anchor="middle">Functions</text>
  </g>
  <g class="feature" transform="translate(673,1512)">
    <rect class="feature-frame" width="215" height="175"/>
    <polygon class="feature-cap" points="0,0 215,0 215,3 107.5,18 0,3"/>
    <polygon class="feature-cap" points="0,175 215,175 215,172 107.5,157 0,172"/>
    <g class="icon" transform="translate(107.5,60)">
      <path d="M-14,-28 h14 l5,6 h27 v36 h-46 z" opacity="0.55"/>
      <path d="M-24,-20 h14 l5,6 h27 v38 h-46 z" opacity="0.8"/>
      <path d="M-34,-12 h16 l5,6 h31 v42 h-52 z"/>
      <rect x="-10" y="26" width="3" height="3" fill="#ffffff"/>
      <rect x="-4" y="26" width="3" height="3" fill="#ffffff"/>
    </g>
    <text class="feature-label" x="107.5" y="116" font-size="22" text-anchor="middle">Vehicle Data</text>
  </g>

  <!-- Feature grid: row 2 -->
  <g class="feature" transform="translate(87,1744)">
    <rect class="feature-frame" width="215" height="175"/>
    <polygon class="feature-cap" points="0,0 215,0 215,3 107.5,18 0,3"/>
    <polygon class="feature-cap" points="0,175 215,175 215,172 107.5,157 0,172"/>
    <g class="icon" transform="translate(107.5,60)">
      <circle r="31"/>
      <g stroke="#ffffff" stroke-width="3.5">
        <line x1="-8" y1="-30" x2="14" y2="-4"/>
        <line x1="26" y1="-16" x2="10" y2="13"/>
        <line x1="22" y1="22" x2="-12" y2="16"/>
        <line x1="-20" y1="24" x2="-16" y2="-8"/>
        <line x1="-30" y1="-4" x2="2" y2="-18"/>
      </g>
    </g>
    <text class="feature-label" x="107.5" y="116" font-size="22" text-anchor="middle">Optics Camera</text>
  </g>
  <g class="feature" transform="translate(380,1744)">
    <rect class="feature-frame" width="215" height="175"/>
    <polygon class="feature-cap" points="0,0 215,0 215,3 107.5,18 0,3"/>
    <polygon class="feature-cap" points="0,175 215,175 215,172 107.5,157 0,172"/>
    <g class="icon" transform="translate(107.5,60)">
      <circle cx="-16" cy="-19" r="12"/>
      <circle cx="10" cy="-19" r="12"/>
      <circle cx="-16" cy="-19" r="5" fill="#ffffff"/>
      <circle cx="10" cy="-19" r="5" fill="#ffffff"/>
      <rect x="-30" y="-6" width="48" height="36" rx="4"/>
      <polygon points="18,6 32,-4 32,28 18,18"/>
    </g>
    <text class="feature-label" x="107.5" y="116" font-size="22" text-anchor="middle">Full Data</text>
    <text class="feature-label" x="107.5" y="143" font-size="22" text-anchor="middle">Recording</text>
  </g>
  <g class="feature" transform="translate(673,1744)">
    <rect class="feature-frame" width="215" height="175"/>
    <polygon class="feature-cap" points="0,0 215,0 215,3 107.5,18 0,3"/>
    <polygon class="feature-cap" points="0,175 215,175 215,172 107.5,157 0,172"/>
    <g class="icon" transform="translate(107.5,60)">
      <circle cx="-6" cy="-10" r="11"/>
      <g stroke="var(--purple-band)" stroke-width="3" stroke-linecap="round">
        <line x1="-6" y1="-32" x2="-6" y2="-26"/>
        <line x1="-27" y1="-10" x2="-22" y2="-10"/>
        <line x1="-21" y1="-25" x2="-17" y2="-21"/>
        <line x1="9" y1="-25" x2="5" y2="-21"/>
        <line x1="-21" y1="5" x2="-17" y2="1"/>
        <line x1="-6" y1="28" x2="-9" y2="34"/>
        <line x1="2" y1="28" x2="-1" y2="34"/>
        <line x1="10" y1="28" x2="7" y2="34"/>
      </g>
      <path d="M-14,22 a10,10 0 0 1 4,-19 a15,15 0 0 1 28,-2 a11,11 0 0 1 12,21 z"/>
    </g>
    <text class="feature-label" x="107.5" y="116" font-size="22" text-anchor="middle">All-Weather &amp;</text>
    <text class="feature-label" x="107.5" y="143" font-size="22" text-anchor="middle">All-Terrain</text>
  </g>

  <!-- Soft background texture behind notes -->
  <g role="img" aria-label="Faint lavender network of connected dots and triangles">
    <rect x="0" y="1930" width="972" height="220" fill="url(#mistGrad)"/>
  </g>

  <text class="note" x="486" y="1983" font-size="20" text-anchor="middle" textLength="695" lengthAdjust="spacingAndGlyphs">Full Instructor Overview with Audio, Visuals, Vehicle Data, and Camera Control</text>
  <text class="note" x="486" y="2012" font-size="20" text-anchor="middle" textLength="445" lengthAdjust="spacingAndGlyphs">Air-Conditioned Instructor Command Workstation</text>

  <!-- Call to action and footer -->
  <rect x="0" y="2141" width="120" height="7" fill="#d8cdf2"/>
  <rect x="140" y="2141" width="120" height="7" fill="#b9a6e6"/>
  <rect x="262" y="2141" width="378" height="7" fill="var(--purple-band)"/>
  <polygon points="675,2103 972,2103 972,2158 635,2158" fill="var(--purple-band)"/>
  <text class="cta" x="810" y="2150" font-size="42" text-anchor="middle" textLength="200" lengthAdjust="spacingAndGlyphs">CALL NOW</text>

  <rect x="0" y="2158" width="972" height="129" fill="url(#bandGrad)"/>
  <g transform="translate(37,2195)" fill="#ffffff">
    <path d="M0,-18 a13,13 0 0 1 13,13 c0,10 -13,24 -13,24 c0,0 -13,-14 -13,-24 a13,13 0 0 1 13,-13 z"/>
    <circle cx="0" cy="-5" r="5" fill="var(--purple-band)"/>
  </g>
  <text class="address" x="66" y="2192" font-size="19">Lena Hartwig</text>
  <text class="address" x="66" y="2215" font-size="19">Ahornstrasse 12B</text>
  <text class="address" x="66" y="2239" font-size="19">85110 Kelbach</text>
  <text class="address" x="66" y="2262" font-size="19">GERMANY</text>

  <text class="phone" x="490" y="2232" font-size="66" textLength="425" lengthAdjust="spacingAndGlyphs">49 1785502916</text>
  <text class="web" x="490" y="2260" font-size="24" textLength="420" lengthAdjust="spacingAndGlyphs">WWW.BRELLOWTRACKLINE.COM</text>
</svg>
</body>
</html>
```